Marlowby Services Website Design

We have most content but require a professional design. We have a logo already and will need it utilized along with several of the photos from the attached documentation.
First page should have our mission and Vision and the synapsis provided in the word document. Visitors will be prompted to select from one of our 3 divisions from this page.
Each division will have the same list of tabs : About, Services, Safety, Careers and Contact.
Photos on each divisions page should be representative of the divisions offerings. The word doc attached contains the requested content and we are open to edits that would complement and fill the website.
I like the Quorvane site www.quorvane.example - they are our competition so cant be modeled directly after this.
Please include prompts to request quote at each service page. align the format of the geotechnical page to the other 2 divisions.
I used chat gpt for some of the content so will need it optimized for SCO.

```html
<!DOCTYPE html>
<html lang="en">
<head>
<meta charset="utf-8">
<title>Marlowby Services</title>
<link rel="stylesheet" href="https://fonts.googleapis.com/css2?family=Lato:wght@400;700;900&family=Oswald:wght@500&display=swap">
<style>
:root{
  --red:#e8262b;
  --ink:#1c1c1c;
  --body:#333333;
  --muted:#555555;
  --soft:#f5f5f5;
  --footer:#333333;
  --line:#e4e4e4;
  --white:#ffffff;
}
*{box-sizing:border-box;margin:0;padding:0}
html,body{width:1200px;height:2629px;overflow:hidden}
body{position:relative;font-family:'Lato',sans-serif;color:var(--body);background:var(--white)}
.abs{position:absolute}
.btn{position:absolute;display:flex;align-items:center;justify-content:center;width:106px;height:35px;background:var(--red);color:var(--white);font-size:13px;font-weight:700;text-decoration:none}

/* hero */
.hero{position:absolute;left:0;top:0;width:1200px;height:565px;background:#050608;overflow:hidden}
.hero-photo{position:absolute;left:420px;top:0;width:780px;height:565px;
  background:linear-gradient(90deg,#050608 0%,rgba(5,6,8,0) 35%),
  radial-gradient(ellipse at 42% 62%,#e8a23a 0%,#9a5a32 14%,rgba(40,50,70,0) 40%),
  linear-gradient(180deg,#2b3d57 0%,#4d6a86 45%,#384a5c 70%,#8a6a34 90%,#2a2a2a 100%)}
.logo{position:absolute;left:140px;top:22px;font-family:'Lato',sans-serif;font-weight:900;font-size:44px;letter-spacing:4px;color:var(--white);line-height:40px}
.nav{position:absolute;top:25px;left:653px;display:flex;align-items:center;height:35px}
.nav a{color:var(--white);font-size:13px;text-decoration:none;margin-right:33px}
.nav .nav-cta{margin:0;background:var(--white);color:var(--red);font-weight:700;width:106px;height:35px;display:flex;align-items:center;justify-content:center;margin-left:-1px}
.hero h1{position:absolute;left:142px;top:170px;font-family:'Oswald',sans-serif;font-weight:500;font-size:46px;line-height:54px;color:var(--white)}
.hero .sub{position:absolute;left:141px;top:340px;width:440px;font-size:20px;line-height:27px;color:var(--white);font-weight:700}

/* services */
.section-title{position:absolute;left:0;width:1200px;text-align:center;color:var(--red);font-size:31px;font-weight:700}
.services-sub{position:absolute;left:0;top:664px;width:1200px;text-align:center;font-size:13px;font-weight:700;color:var(--ink)}
.svc{position:absolute;top:700px;width:240px;height:140px;text-align:center}
.svc+.svc{border-left:1px solid var(--line)}
.svc svg{display:block;margin:10px auto 0}
.svc h3{font-size:14.5px;font-weight:700;color:var(--ink);margin-top:8px}
.svc p{font-size:11px;line-height:19px;color:var(--muted);margin-top:3px}

/* vision */
.vision-photo{position:absolute;left:0;top:983px;width:565px;height:437px;background:linear-gradient(180deg,#3d4a3a 0%,#6b7763 35%,#9a9588 60%,#a39d92 100%)}
.vision-text{position:absolute;left:565px;top:983px;width:635px;height:437px;background:var(--soft)}
.vision-text h2{position:absolute;left:57px;color:var(--red);font-size:21px;font-weight:700}
.vision-text p{position:absolute;left:57px;width:440px;font-size:12.6px;line-height:22px;color:var(--ink)}

/* divisions */
.div-band{position:absolute;left:0;top:1505px;width:1200px;height:353px;background:linear-gradient(180deg,#4a5156 0%,#3a423c 50%,#4b4d44 100%)}
.div-panel{position:absolute;left:140px;top:1645px;width:919px;height:400px;background:var(--white)}
.card{position:absolute;top:1680px;width:275px}
.card .ph{width:275px;height:212px}
.card h3{color:var(--red);font-size:17.5px;font-weight:700;margin:16px 0 0 6px}
.card p{font-size:11px;line-height:19px;color:var(--ink);margin:7px 0 0 6px;width:270px}
.card .more{display:flex;align-items:center;gap:8px;color:var(--red);font-size:13px;font-weight:700;margin:6px 0 0 6px}

/* callout */
.footer{position:absolute;left:0;top:2270px;width:1200px;height:359px;background:var(--footer)}
.callout{position:absolute;left:183px;top:2105px;width:834px;height:235px;background:var(--soft);box-shadow:0 0 14px rgba(0,0,0,.08);border-bottom:8px solid #9a9a9a}
.callout h2{position:absolute;left:0;top:46px;width:834px;text-align:center;font-size:22.5px;line-height:30px;font-weight:700;color:var(--ink)}
.callout h2 .brand{color:var(--red)}

/* footer */
.f-head{position:absolute;top:2386px;font-size:18px;font-weight:700;color:var(--white)}
.f-rule{position:absolute;top:2418px;height:1px;background:#5a5a5a}
.f-rule::before{content:"";position:absolute;left:0;top:-1px;width:26px;height:3px;background:var(--red)}
.f-link{position:absolute;font-size:13px;color:var(--white)}
.f-link::before{content:"»";font-size:11px;margin-right:8px}
.f-label{position:absolute;font-size:13px;font-weight:700;color:var(--white)}
.f-val{position:absolute;font-size:13px;color:var(--white)}
.f-logo{position:absolute;left:827px;top:2383px;font-weight:900;font-size:30px;letter-spacing:3px;color:var(--red)}
.f-divider{position:absolute;left:140px;top:2574px;width:919px;height:1px;background:#5a5a5a}
.copy{position:absolute;left:144px;top:2595px;font-size:13px;color:var(--white)}
.social{position:absolute;top:2589px;width:28px;height:28px;border-radius:50%;background:var(--red)}
</style>
</head>
<body>

<header class="hero">
  <div class="hero-photo" role="img" aria-label="Field technician in hard hat and safety vest in front of an industrial refinery at sunset"></div>
  <div class="logo">MARLOWBY</div>
  <nav class="nav">
    <a href="#">Home</a><a href="#">About Us</a><a href="#">Safety</a><a href="#">Careers</a>
    <a class="nav-cta" href="#">Contact Us</a>
  </nav>
  <h1>Delivering Safe,<br>Reliable Aerial Access<br>&amp; Maintenance Services</h1>
  <p class="sub">To Oil &amp; Gas,Construction, Utility, &amp; Renewable Energy Sector</p>
  <a class="btn" style="left:141px;top:409px" href="#">Contact Us</a>
</header>

<section>
  <h2 class="section-title" style="top:620px">Marlowby Services</h2>
  <p class="services-sub">Delivering Safe Reliable Aerial Access And Maintenance Services</p>

  <div class="svc" style="left:120px">
    <svg width="52" height="52" viewBox="0 0 52 52" fill="none" stroke="#e8262b" stroke-width="2"><rect x="4" y="20" width="44" height="28"/><rect x="12" y="6" width="8" height="14"/><rect x="28" y="12" width="10" height="8"/><path d="M10 48V36h8v12M28 30h12M28 38h12"/></svg>
    <h3>Oil &amp; Gas</h3>
    <p>Lorem ipsum dolor sit amet, consectetur<br>adipiscing egestas metus auctor elit.</p>
  </div>
  <div class="svc" style="left:360px">
    <svg width="56" height="56" viewBox="0 0 56 56" fill="none" stroke="#e8262b" stroke-width="2"><path d="M6 8h30M10 8v8h22V8M21 16v4M14 54l7-34M28 54l-7-34M12 44h18M16 32h10"/><path d="M40 14h10v22H40zM4 54h48"/></svg>
    <h3>Construction</h3>
    <p>Lorem ipsum dolor sit amet, consectetur<br>adipiscing egestas metus auctor elit.</p>
  </div>
  <div class="svc" style="left:600px">
    <svg width="52" height="52" viewBox="0 0 52 52" fill="none" stroke="#e8262b" stroke-width="2"><circle cx="26" cy="26" r="14"/><path d="M26 4v6M26 42v6M4 26h6M42 26h6M10 10l4 4M38 38l4 4M42 10l-4 4M14 38l-4 4"/><path d="M22 20v12M30 20v12"/></svg>
    <h3>Utility</h3>
    <p>Lorem ipsum dolor sit amet, consectetur<br>adipiscing egestas metus auctor elit.</p>
  </div>
  <div class="svc" style="left:840px">
    <svg width="52" height="52" viewBox="0 0 52 52" fill="none" stroke="#e8262b" stroke-width="2"><path d="M8 26a18 18 0 0 1 30-13M44 26a18 18 0 0 1-30 13"/><path d="M38 6v7h-7M14 46v-7h7"/><path d="M26 34c-6-4-6-12 0-16c6 4 6 12 0 16zM26 22v14"/></svg>
    <h3>Renewable Energy Industries</h3>
    <p>Lorem ipsum dolor sit amet, consectetur<br>adipiscing egestas metus auctor elit.</p>
  </div>

  <a class="btn" style="left:547px;top:864px" href="#">Contact Us</a>
</section>

<section>
  <div class="vision-photo" role="img" aria-label="White boom truck parked on a gravel lot in front of a forest"></div>
  <div class="vision-text">
    <h2 style="top:44px">Our Vision</h2>
    <p style="top:74px">To be the leading provider of aerial access, geotechnical drilling, and service solutions, setting the standard for excellence in safety, efficiency, and environmental stewardship.</p>
    <h2 style="top:157px">Our Mission</h2>
    <p style="top:187px">At Marlowby, our mission is to deliver unparalleled aerial access, geotechnical drilling, and service and maintenance solutions, consistently exceeding our clients' expectations. We strive to achieve this by investing in cutting-edge technology, fostering a culture of safety and continuous improvement, and prioritizing environmental sustainability. Through collaboration, integrity, and dedication, we aim to contribute to the success of our clients while maintaining the highest standards of quality and professionalism.</p>
    <a class="btn" style="left:57px;top:355px" href="#">Contact Us</a>
  </div>
</section>

<section>
  <div class="div-band" role="img" aria-label="Aerial view of a rural road and fields with a worker in a lift basket"></div>
  <h2 class="section-title" style="top:1583px;color:var(--white);font-weight:400;font-size:32px">Our Divisions</h2>
  <div class="div-panel"></div>

  <article class="card" style="left:175px">
    <div class="ph" role="img" aria-label="Aerial lift extended beside a wind turbine tower" style="background:linear-gradient(180deg,#3f78c4 0%,#8fb3dc 70%,#7d7a5e 100%)"></div>
    <h3>Aerial Access</h3>
    <p>Marlowby is a full-service wind energy service provider specializing in blade access &amp; repair, service and maintenance, and trouble shooting on most wind turbine platforms.</p>
    <div class="more">Read More <svg width="18" height="8" viewBox="0 0 18 8" fill="none" stroke="#e8262b" stroke-width="1.5"><path d="M0 4h16M13 1l3 3-3 3"/></svg></div>
  </article>
  <article class="card" style="left:462px">
    <div class="ph" role="img" aria-label="Red tracked geotechnical drill rig in green brush" style="background:linear-gradient(180deg,#2c4a22 0%,#3f6b2e 45%,#8a2a26 70%,#2e3a22 100%)"></div>
    <h3>Geotechnical Drilling</h3>
    <p>Lorem ipsum dolor sit amet onsctetur adipiscing elit. Nullam porta turpis dui, ut ultricies nisi soicitudin et. Quisque tellus vitae mauris veenatis blandit. Nunc accumsan nisi ut pellentesque placerat.</p>
    <div class="more">Read More <svg width="18" height="8" viewBox="0 0 18 8" fill="none" stroke="#e8262b" stroke-width="1.5"><path d="M0 4h16M13 1l3 3-3 3"/></svg></div>
  </article>
  <article class="card" style="left:750px">
    <div class="ph" role="img" aria-label="Lift boom reaching toward a wind turbine against blue sky" style="background:linear-gradient(160deg,#1f5fbf 0%,#3b7ad6 55%,#6f9fe0 100%)"></div>
    <h3>Renewable Energy Services</h3>
    <p>Lorem ipsum dolor sit amet onsctetur adipiscing elit. Nullam porta turpis dui, ut ultricies nisi soicitudin et. Quisque tellus vitae mauris veenatis blandit. Nunc accumsan nisi ut pellentesque placerat.</p>
    <div class="more">Read More <svg width="18" height="8" viewBox="0 0 18 8" fill="none" stroke="#e8262b" stroke-width="1.5"><path d="M0 4h16M13 1l3 3-3 3"/></svg></div>
  </article>
</section>

<footer class="footer"></footer>

<section class="callout">
  <h2><span class="brand">MARLOWBY</span> is a Full Service Wind Energy Service Provider<br>Specializing In Blade Access And Repair, Service And Maintenance,<br>And Trouble Shooting On Most Wind Turbine Platforms.</h2>
  <a class="btn" style="left:392px;top:155px" href="#">Contact Us</a>
</section>

<div class="f-head" style="left:143px">Quick Links</div>
<div class="f-rule" style="left:143px;width:110px"></div>
<div class="f-link" style="left:145px;top:2437px">Home</div>
<div class="f-link" style="left:145px;top:2465px">About</div>
<div class="f-link" style="left:145px;top:2493px">Services</div>
<div class="f-link" style="left:271px;top:2437px">Safety</div>
<div class="f-link" style="left:271px;top:2465px">Careers</div>
<div class="f-link" style="left:271px;top:2493px">Contact Us</div>

<div class="f-head" style="left:506px">Contact Details</div>
<div class="f-rule" style="left:506px;width:142px"></div>
<svg class="abs" style="left:506px;top:2441px" width="13" height="13" viewBox="0 0 24 24" fill="#fff"><path d="M6.6 10.8a15.2 15.2 0 0 0 6.6 6.6l2.2-2.2c.3-.3.7-.4 1-.2 1.1.4 2.3.6 3.6.6.6 0 1 .4 1 1V20c0 .6-.4 1-1 1A17 17 0 0 1 3 4c0-.6.4-1 1-1h3.5c.6 0 1 .4 1 1 0 1.3.2 2.5.6 3.6.1.3 0 .7-.2 1z"/></svg>
<div class="f-label" style="left:527px;top:2441px">Phone</div>
<div class="f-val" style="left:527px;top:2461px">(555)-014-2290</div>
<svg class="abs" style="left:506px;top:2493px" width="14" height="11" viewBox="0 0 14 11" fill="none" stroke="#fff" stroke-width="1.5"><rect x="1" y="1" width="12" height="9"/><path d="M1 1l6 5 6-5"/></svg>
<div class="f-label" style="left:527px;top:2491px">Email</div>
<div class="f-val" style="left:527px;top:2511px">career@marlowbyservices.example</div>

<div class="f-logo">MARLOWBY</div>
<svg class="abs" style="left:827px;top:2433px" width="11" height="15" viewBox="0 0 11 15" fill="#fff"><path d="M5.5 0A5.5 5.5 0 0 0 0 5.5C0 9.6 5.5 15 5.5 15S11 9.6 11 5.5A5.5 5.5 0 0 0 5.5 0zm0 7.6a2.1 2.1 0 1 1 0-4.2 2.1 2.1 0 0 1 0 4.2z"/></svg>
<div class="f-val" style="left:846px;top:2432px;line-height:20px">218 Ridgeline Road Alder Flats<br>AB T0C-4X1</div>

<div class="f-divider"></div>
<div class="copy">© 2024 MARLOWBY. All Rights Reserved.</div>
<div class="social" style="left:925px" aria-label="Social link"></div>
<div class="social" style="left:961px" aria-label="Social link"></div>
<div class="social" style="left:996px" aria-label="Social link"></div>
<div class="social" style="left:1031px" aria-label="Social link"></div>

</body>
</html>
```